New Business Card Design for Manufacturing

We are an engineering/manufacturing company that offers Advanced machining/assembly/engineering services, as well as innovative products for the heavy duty engine cooling markets.

We are looking to get a new business card designed that is clean and modern looking, but still fits the wide range of technical/skilled work we do.

- We hope to use this design as the base for other design work in new Presentations, web, and print work.

Industry/Entity Type

Engineering

Contact Information for Business Card

Our preferred color of blue is (RGB) 22/71/159 but can vary slightly from that color. Our content will be our Logo and full company name (Vantrell Forge Works, Inc.), company address, name, job title, phone number with extension, cell number, fax number, website, and email address on the cards.
We'd like the full company name next to the logo, but we are open to other interpretations of that layout.
Preferably, we would like the back side to be clean with just our logo, and the front to contain all of the contact information.

Colors
2f74b4
0355a3
85abd2

Requirements
Must have
• - Logo, company name, needed content - We are open to interpretation beyond that.
• - Standard size business card.
• - Horizontal orientation.
• - Enough space for lengthy names / job titles (for example, a job title could read "Directory of Human Resources" or "V.P. of Governmental Affairs"). We need this to look clean, whether the title be short (CEO) or long (as described above).

```html
<!DOCTYPE html>
<html lang="en">
<head>
<meta charset="utf-8">
<title>Vantrell Forge Works – Business Cards</title>
<link href="https://fonts.googleapis.com/css2?family=Lato:wght@400;700;900&display=swap" rel="stylesheet">
<style>
  :root {
    --brand-blue: #16479f;
    --ink-blue: #1a4aa6;
    --paper: #ffffff;
    --backdrop: #35302c;
  }
  * { box-sizing: border-box; margin: 0; padding: 0; }
  html, body { width: 1200px; height: 780px; overflow: hidden; }
  body {
    background: var(--backdrop);
    font-family: "Lato", Arial, sans-serif;
    position: relative;
  }
  .card {
    position: absolute;
    width: 525px;
    height: 300px;
    border-radius: 2px;
  }
  /* Back side */
  .card-back {
    left: 60px; top: 110px;
    background: var(--brand-blue);
    color: var(--paper);
  }
  .card-back .brand {
    position: absolute; left: 120px; top: 92px;
  }
  .brand-name {
    font-weight: 900;
    text-transform: uppercase;
    line-height: 1.02;
    letter-spacing: 0.5px;
  }
  .card-back .brand-name { font-size: 30px; }
  .brand-tagline {
    font-weight: 700;
    text-transform: uppercase;
    font-size: 10px;
    letter-spacing: 1px;
    margin-top: 8px;
  }
  .card-back .website {
    position: absolute; left: 120px; top: 215px;
    font-size: 12px; letter-spacing: 3.5px;
  }
  /* Front side */
  .card-front {
    left: 615px; top: 380px;
    background: var(--paper);
    color: var(--ink-blue);
  }
  .person { position: absolute; left: 28px; top: 26px; }
  .person-name { font-size: 17px; font-weight: 700; text-transform: uppercase; }
  .person-title { font-size: 12px; line-height: 1; }
  .card-front .brand {
    position: absolute; right: 30px; top: 98px; text-align: left;
  }
  .card-front .brand-name { font-size: 21px; }
  .card-front .brand-tagline { font-size: 8px; }
  .contacts {
    position: absolute; left: 28px; top: 136px;
    list-style: none; font-size: 13px; line-height: 17px;
  }
  .contacts li { display: flex; align-items: center; gap: 6px; }
  .contacts svg { width: 11px; height: 11px; fill: var(--ink-blue); }
  .divider {
    position: absolute; left: 28px; right: 28px; top: 200px;
    border-top: 1px solid var(--ink-blue);
  }
  .address {
    position: absolute; right: 28px; bottom: 24px;
    text-align: right; font-size: 14px; line-height: 19px;
  }
</style>
</head>
<body>
  <section class="card card-back" aria-label="Card back">
    <div class="brand">
      <div class="brand-name">Vantrell<br>Forge Works<br>Inc.</div>
      <div class="brand-tagline">Built to Run Further</div>
    </div>
    <div class="website">www.vantrellforge.com</div>
  </section>

  <section class="card card-front" aria-label="Card front">
    <div class="person">
      <div class="person-name">Marlo Quint</div>
      <div class="person-title">Owner</div>
    </div>
    <div class="brand">
      <div class="brand-name">Vantrell Forge<br>Works, Inc.</div>
      <div class="brand-tagline">Built to Run Further</div>
    </div>
    <ul class="contacts">
      <li><svg viewBox="0 0 12 12"><path d="M3 0h6a1 1 0 0 1 1 1v10a1 1 0 0 1-1 1H3a1 1 0 0 1-1-1V1a1 1 0 0 1 1-1zm0 1.5v8h6v-8z"/></svg>(555) 014-2290</li>
      <li><svg viewBox="0 0 12 12"><path d="M3 0h6v3H3zM1 4h10v5H9v3H3V9H1zm3 4v3h4V8z"/></svg>(555) 014-2291</li>
      <li><svg viewBox="0 0 12 12"><path d="M0 2h12v8H0zm1 1v.5l5 3.5 5-3.5V3z"/></svg>info@vantrellforge.com</li>
    </ul>
    <div class="divider"></div>
    <address class="address" style="font-style:normal">PO BOX 418 Harrow Lane<br>2nd street Corriston</address>
  </section>
</body>
</html>
```